Kestrel Facilities Business Card Design

We would now like to design business cards with the new Kestrel Facilities logo

Target Market(s)

Professional

Industry/Entity Type

Professional services

Contact Information for Business Card

Employee name, title, phone number, email address, corporate office address and logo.

Font styles to use
Sans Serif

Colors
0054AA
0677BA
7BADD7
CADEEF
E8F1F8

Requirements
Must have
• My logo
Should not have
• any other pictures or images besides my logo

```html
<!DOCTYPE html>
<html lang="en">
<head>
<meta charset="utf-8">
<title>Kestrel Facilities Business Card</title>
<link rel="stylesheet" href="https://fonts.googleapis.com/css2?family=Lato:wght@400;700&family=Oswald:wght@500;600&display=swap">
<style>
  :root {
    --blue: #0677BA;
    --blue-bright: #1a7fe0;
    --blue-deep: #0054AA;
    --ink: #1c1c1c;
    --rule: #9a9a9a;
    --paper: #ffffff;
    --stage: #2b2b2b;
    --back-dark: #0d0d0d;
    --back-mid: #1e1e1e;
  }
  * { margin: 0; padding: 0; box-sizing: border-box; }
  html, body { width: 1200px; height: 1108px; overflow: hidden; }
  body { background: var(--stage); position: relative; font-family: "Lato", sans-serif; }

  .card {
    position: absolute;
    top: 194px;
    width: 440px;
    height: 720px;
    border-radius: 26px;
    overflow: hidden;
  }
  .card-front { left: 120px; background: var(--paper); text-align: center; color: var(--ink); }
  .card-back { left: 640px; background: var(--back-dark); }

  .brand-name {
    position: absolute;
    top: 110px; left: 0; right: 0;
    font-family: "Oswald", sans-serif;
    font-weight: 600;
    color: var(--blue-bright);
    text-transform: uppercase;
    line-height: 1;
  }
  .brand-name .brand-line-main { display: block; font-size: 88px; letter-spacing: 2px; }
  .brand-name .brand-line-sub { display: block; font-size: 52px; letter-spacing: 9px; margin-top: 12px; }

  .person { position: absolute; top: 392px; left: 0; right: 0; }
  .person-name {
    font-family: "Oswald", sans-serif;
    font-weight: 500;
    font-size: 38px;
    color: var(--blue-bright);
    text-transform: uppercase;
    line-height: 1.05;
  }
  .person-title { font-size: 20px; margin-top: 2px; }

  .contact-divider {
    position: absolute; top: 478px; left: 56px; right: 56px;
    display: flex; align-items: center; gap: 8px;
  }
  .contact-divider .rule { flex: 1; height: 1px; background: var(--rule); }
  .contact-icon {
    width: 28px; height: 28px; border-radius: 4px;
    background: var(--blue-bright);
    display: flex; align-items: center; justify-content: center;
  }

  .contact-list { position: absolute; top: 522px; left: 0; right: 0; list-style: none; font-size: 20px; line-height: 1.35; }
  .contact-list .web-accent { color: var(--blue-bright); }

  .address-rule { position: absolute; top: 620px; left: 56px; right: 56px; height: 1px; background: var(--rule); }
  .address { position: absolute; top: 634px; left: 0; right: 0; font-style: normal; font-size: 20px; line-height: 1.35; }

  .back-pattern {
    position: absolute; inset: 0;
    background: linear-gradient(150deg, var(--back-mid) 0%, var(--back-dark) 55%, #050505 100%);
  }
  .back-brand {
    position: absolute; right: 60px; bottom: 90px;
    font-family: "Oswald", sans-serif;
    font-weight: 600;
    font-size: 30px;
    color: var(--blue-bright);
    text-transform: uppercase;
    letter-spacing: 1px;
  }
</style>
</head>
<body>
  <section class="card card-front">
    <div class="brand-name">
      <span class="brand-line-main">Kestrel</span>
      <span class="brand-line-sub">Facilities</span>
    </div>

    <div class="person">
      <h1 class="person-name">Daniel Hartwell</h1>
      <p class="person-title">Managing Director</p>
    </div>

    <div class="contact-divider">
      <span class="rule"></span>
      <span class="contact-icon" aria-label="Phone">
        <svg width="18" height="18" viewBox="0 0 24 24"><path fill="#fff" d="M6.6 10.8a15 15 0 0 0 6.6 6.6l2.2-2.2c.3-.3.7-.4 1-.2 1.1.4 2.3.6 3.6.6.6 0 1 .4 1 1V20c0 .6-.4 1-1 1A17 17 0 0 1 3 4c0-.6.4-1 1-1h3.5c.6 0 1 .4 1 1 0 1.3.2 2.5.6 3.6.1.3 0 .7-.2 1z"/></svg>
      </span>
      <span class="contact-icon" aria-label="Email">
        <svg width="18" height="18" viewBox="0 0 24 24"><rect x="3" y="6" width="18" height="12" fill="none" stroke="#fff" stroke-width="2"/><path d="M3 6l9 7 9-7" fill="none" stroke="#fff" stroke-width="2"/></svg>
      </span>
      <span class="contact-icon" aria-label="Website">
        <svg width="18" height="18" viewBox="0 0 24 24"><circle cx="12" cy="12" r="9" fill="none" stroke="#fff" stroke-width="2"/><path d="M3 12h18M12 3c3 3 3 15 0 18M12 3c-3 3-3 15 0 18" fill="none" stroke="#fff" stroke-width="1.5"/></svg>
      </span>
      <span class="rule"></span>
    </div>

    <ul class="contact-list">
      <li>020-7946 0321</li>
      <li>info@kestrelfacilities.com</li>
      <li>www.<span class="web-accent">kestrelfacilities</span>.com</li>
    </ul>

    <div class="address-rule"></div>
    <address class="address">18 Harbour Lane, Suite 4<br>Bristol BS1 4QA, UK</address>
  </section>

  <section class="card card-back">
    <div class="back-pattern" role="img" aria-label="Glossy black embossed repeating brand pattern"></div>
    <p class="back-brand">Kestrel Facilities</p>
  </section>
</body>
</html>
```